Need Amazing Website for Consulting Company

We need an amazing website design for a Human Resources Consulting Company. This will be geared towards a more professional crowd, but we don't want it to be overly corporate and stuffy: Just, clean and professional and amazing. Please use the video link below for further instruction.

http://clipharbor.net/v/kLm9PxQz

Thank You.

PS Logo file has been attached.

Target Market(s)

The target marketing is small business owners who have employees. These owners cant afford an in-house HR person so they would hire this client to consult and do the work for them.

Industry/Entity Type

It Company

Font styles to use
Sans Serif

Requirements
Must have
• Please watch video:

Must have spot for video on homepage.
Nice to have
• Clean, professional, but not overly corporate, we want a personal and fun feel to this site a bit to separate them from all the other executive type sites. This site should have some LIFE to it and reflect a local brand that is doing great things.
Should not have
• Should not be just a corporate site, should not be overly stuffy, should not be overly boring.

```html
<!DOCTYPE html>
<html lang="en">
<head>
<meta charset="utf-8">
<title>Mesa Ridge HR Consulting</title>
<link rel="stylesheet" href="https://fonts.googleapis.com/css2?family=Open+Sans:ital,wght@0,400;0,600;0,700;0,800;1,700&display=swap">
<style>
:root{
  --red:#b81429;
  --red-dark:#9c0f22;
  --ink:#111;
  --text:#333;
  --grey-btn:#666;
  --page:#f1f1f1;
  --card:#fff;
  --line:#dcdcdc;
  --foot:#151515;
  --foot-text:#8a8a8a;
  --foot-head:#cfcfcf;
}
*{box-sizing:border-box;margin:0;padding:0}
html,body{width:1034px;height:1200px;overflow:hidden}
body{font-family:"Open Sans",Arial,sans-serif;color:var(--text);background:var(--page);position:relative}
.wrap{width:844px;margin:0 auto;position:relative}

/* header */
.site-header{height:117px;background:#fff}
.site-header .wrap{height:117px;display:flex;justify-content:space-between;align-items:center}
.brand{display:flex;align-items:center;gap:10px;font-weight:800;font-size:24px;color:var(--ink);letter-spacing:.5px;line-height:1}
.brand-mark{width:26px;height:26px;border-radius:50%;background:var(--red)}
.header-right{text-align:right}
.social-top{display:flex;gap:4px;justify-content:flex-end;margin-bottom:12px}
.social-top span{width:22px;height:22px;border-radius:50%;display:block}
.social-top span:nth-child(1){background:#3b5a9a}
.social-top span:nth-child(2){background:#2aa3dc}
.social-top span:nth-child(3){background:#d34836}
.call{font-weight:700;font-size:14px;color:var(--ink)}
.call b{color:var(--red)}

/* tagline band */
.tagline{height:49px;background:#000;color:#fff;display:flex;align-items:center;justify-content:center;font-size:25px;letter-spacing:1px;font-weight:400}
.tagline em{font-style:italic;font-weight:700;margin:0 12px;letter-spacing:0}

/* nav */
.main-nav{height:31px;background:linear-gradient(#c8172e,var(--red-dark))}
.main-nav ul{list-style:none;display:flex;height:31px}
.main-nav li{color:#fff;font-weight:700;font-size:11.5px;padding:0 9px;display:flex;align-items:center;border-left:1px solid rgba(255,255,255,.25)}
.main-nav li:first-child{padding-left:0;border-left:0}

/* hero */
.hero{height:312px;position:relative}
.hero-photo{position:absolute;inset:0;background:linear-gradient(90deg,#b9c79a 0%,#e9ece3 30%,#d9cfc4 50%,#5a3a30 62%,#c89a84 72%,#e8e6e2 90%,#dfe3e8 100%)}
.hero .wrap{display:flex;height:312px}
.video{position:absolute;left:1px;top:18px;width:400px;height:275px;background:var(--red)}
.video .play{position:absolute;left:173px;top:112px}
.video-bar{position:absolute;left:0;right:0;bottom:0;height:22px;background:#111;display:flex;align-items:center}
.video-bar .btn{width:31px;display:flex;justify-content:center}
.video-bar .track{flex:1;height:7px;background:#fff;margin:0 16px 0 8px;position:relative}
.video-bar .track::before{content:"";position:absolute;left:0;top:0;bottom:0;width:40px;background:#999}
.video-bar .full{width:30px;display:flex;justify-content:center}
.hero-copy{position:absolute;left:433px;top:66px;width:390px;color:#fff}
.hero-copy h1{font-size:27px;font-weight:700;line-height:1.05;text-shadow:0 1px 3px rgba(0,0,0,.4)}
.hero-copy p{font-size:14.5px;line-height:1.5;margin-top:8px;text-shadow:0 1px 3px rgba(0,0,0,.5)}
.btn-dark{display:inline-block;margin-top:13px;background:#000;color:#fff;font-size:17px;padding:7px 26px;border-radius:4px;box-shadow:0 3px 0 #333}

/* service cards */
.services{display:flex;gap:10px;margin-top:47px}
.card{background:var(--card);border:1px solid var(--line);border-radius:3px;box-shadow:0 1px 3px rgba(0,0,0,.12);position:relative}
.service{width:204px;height:218px;padding:55px 14px 0 18px}
.service .icon{position:absolute;left:64px;top:-35px;width:76px;height:76px;border-radius:50%;background:var(--red);display:flex;align-items:center;justify-content:center}
.card h2{font-size:14px;font-weight:700;color:var(--ink);letter-spacing:.3px;margin-bottom:6px}
.card p{font-size:10.5px;line-height:18px}
.service p{font-size:9.8px;line-height:16.5px;letter-spacing:-.15px}
.news p{line-height:15px}
.news small{display:block;font-size:9.8px;color:#555;margin-bottom:6px;line-height:15px}
.btn-grey{display:inline-block;background:var(--grey-btn);color:#fff;font-size:11px;padding:3px 9px;border-radius:3px;margin-top:10px}
.service .btn-grey{position:absolute;left:20px;bottom:15px;margin-top:0}

/* lower row */
.lower{display:flex;gap:10px;margin-top:13px}
.about{width:630px;height:226px;padding:17px 18px}
.about p{margin-bottom:6px}
.enquire{width:204px;height:226px;padding:17px 18px}
.field{height:23px;border:1px solid #ccc;border-radius:3px;background:linear-gradient(#fff,#f3f3f3);font-size:8.5px;color:#777;padding:5px 9px;margin-bottom:8px}
.field.query{height:68px;position:relative}
.go{position:absolute;right:10px;top:19px;width:33px;height:33px;border-radius:50%;background:var(--red);color:#fff;font-weight:700;font-size:12.5px;display:flex;align-items:center;justify-content:center;box-shadow:0 2px 0 #7a0c1a}

/* footer */
.site-footer{position:absolute;left:0;top:1031px;width:1034px;height:137px;background:var(--foot)}
.site-footer .wrap{display:flex;padding-top:14px}
.site-footer h3{font-size:12px;font-weight:700;color:var(--foot-head);margin-bottom:6px}
.site-footer li{list-style:none;font-size:10.5px;color:var(--foot-text);line-height:20px}
.foot-about{width:389px}
.foot-cols{display:flex}
.foot-cols ul:nth-child(1){width:133px}
.foot-cols ul:nth-child(2){width:105px}
.foot-touch{width:310px}
.social-foot{display:flex;gap:4px}
.social-foot span{width:33px;height:33px;border-radius:50%;background:#fff;display:block}
.copyright{position:absolute;left:0;top:1168px;width:1034px;height:32px;background:#050505;color:var(--foot-text);font-size:8.5px;display:flex;align-items:center;justify-content:center}
</style>
</head>
<body>

<header class="site-header">
  <div class="wrap">
    <div class="brand"><span class="brand-mark"></span>MESA RIDGE HR</div>
    <div class="header-right">
      <div class="social-top" aria-label="Social links"><span></span><span></span><span></span></div>
      <div class="call">CALL NOW! <b>(505) 555-0148</b></div>
    </div>
  </div>
</header>

<div class="tagline">EFFECTIVE. <em>Experienced.</em> EFFICIENT</div>

<nav class="main-nav">
  <div class="wrap">
    <ul>
      <li>HOME</li><li>ABOUT US</li><li>SERVICES</li><li>RECRUITMENT</li><li>CONSULTANCY</li><li>CONTACT US</li>
    </ul>
  </div>
</nav>

<section class="hero">
  <div class="hero-photo" role="img" aria-label="Blurred photo of a smiling professional in a bright office"></div>
  <div class="wrap">
    <div class="video">
      <svg class="play" width="54" height="54" viewBox="0 0 54 54"><circle cx="27" cy="27" r="24" fill="none" stroke="#fff" stroke-width="5"/><path d="M21 16 L37 27 L21 38Z" fill="#fff"/></svg>
      <div class="video-bar">
        <div class="btn"><svg width="11" height="12"><path d="M1 0 L11 6 L1 12Z" fill="#fff"/></svg></div>
        <div class="track"></div>
        <div class="full"><svg width="16" height="13" viewBox="0 0 16 13"><rect x="1" y="1" width="14" height="11" fill="none" stroke="#ccc" stroke-width="1.5"/><path d="M6 5 L12 10 M9 10 H12 V7" stroke="#ccc" stroke-width="1.5" fill="none"/></svg></div>
      </div>
    </div>
    <div class="hero-copy">
      <h1>Human Resources<br>Consulting</h1>
      <p>Lorem Ipsum is simply dummy text of the printing and typesetting industry. Lorem Ipsum has been the industry's standard dummy text ever since the 1500s</p>
      <span class="btn-dark">Learn More</span>
    </div>
  </div>
</section>

<main class="wrap">
  <div class="services">
    <article class="card service">
      <div class="icon"><svg width="38" height="38" viewBox="0 0 38 38" fill="#fff"><circle cx="15" cy="9" r="7"/><path d="M2 34 C2 22 8 19 15 19 C18 19 20 20 22 21 C17 23 16 29 19 34Z"/><circle cx="27" cy="27" r="7" fill="none" stroke="#fff" stroke-width="2.5"/><path d="M27 17V37M17 27H37" stroke="#fff" stroke-width="2"/></svg></div>
      <h2>RECRUITMENT</h2>
      <p>Lorem Ipsum is simply dummy text of the printing and typesetting industry. Lorem Ipsum has been the industry's standard dummy text ever since the 1500s</p>
      <span class="btn-grey">Learn More</span>
    </article>
    <article class="card service">
      <div class="icon"><svg width="42" height="38" viewBox="0 0 42 38"><path d="M21 3 C31 3 38 9 38 17 C38 25 31 31 21 31 C18 31 15 30 13 29 L4 33 L8 26 C5 23 4 20 4 17 C4 9 11 3 21 3Z" fill="none" stroke="#fff" stroke-width="3.5"/><circle cx="14" cy="17" r="2.8" fill="#fff"/><circle cx="21" cy="17" r="2.8" fill="#fff"/><circle cx="28" cy="17" r="2.8" fill="#fff"/></svg></div>
      <h2>CONSULTANCY</h2>
      <p>Lorem Ipsum is simply dummy text of the printing and typesetting industry. Lorem Ipsum has been the industry's standard dummy text ever since the 1500s</p>
      <span class="btn-grey">Learn More</span>
    </article>
    <article class="card service">
      <div class="icon"><svg width="44" height="32" viewBox="0 0 44 32" fill="#fff"><circle cx="10" cy="9" r="5"/><circle cx="34" cy="9" r="5"/><path d="M1 27 C1 18 5 16 10 16 C13 16 14 17 15 18 C12 20 11 24 11 27Z M43 27 C43 18 39 16 34 16 C31 16 30 17 29 18 C32 20 33 24 33 27Z"/><circle cx="22" cy="8" r="6.5"/><path d="M12 31 C12 20 16 17 22 17 C28 17 32 20 32 31Z"/></svg></div>
      <h2>HUMAN RESOURCES</h2>
      <p>Lorem Ipsum is simply dummy text of the printing and typesetting industry. Lorem Ipsum has been the industry's standard dummy text ever since the 1500s</p>
      <span class="btn-grey">Learn More</span>
    </article>
    <article class="card service news">
      <div class="icon"><svg width="38" height="32" viewBox="0 0 38 32"><rect x="2" y="2" width="34" height="28" fill="none" stroke="#fff" stroke-width="3"/><rect x="2" y="2" width="34" height="6" fill="#fff"/><rect x="8" y="12" width="10" height="12" fill="#fff"/><path d="M22 13H31M22 18H31M22 23H31" stroke="#fff" stroke-width="2.5"/></svg></div>
      <h2>LATEST NEWS</h2>
      <p>Lorem Ipsum is simply dummy text of the printing and typesetting</p>
      <small>1/28/2014</small>
      <p>Lorem Ipsum is simply dummy text</p>
      <small>1/28/2014</small>
      <span class="btn-grey">Learn More</span>
    </article>
  </div>

  <div class="lower">
    <section class="card about">
      <h2>ABOUT US</h2>
      <p>Mesa Ridge HR Consulting , LLC. (MRHC) is an experienced consulting agency that is committed to providing businesses with effective and efficient Human Resources support by developing partnerships to meet company’s individual needs. Lorem Ipsum is simply dummy text of the printing and typesetting industry. Lorem Ipsum has been the industry's standard dummy text ever since the 1500s</p>
      <p>Mesa Ridge HR Consulting , LLC. (MRHC) is an experienced consulting agency that is committed to providing businesses with effective and efficient Human Resources support by developing partnerships to meet company’s individual needs. Lorem Ipsum is simply dummy text of the printing and typesetting industry.</p>
      <span class="btn-grey" style="margin-top:5px">Learn More</span>
    </section>
    <section class="card enquire">
      <h2 style="margin-bottom:11px">ENQUIRE NOW</h2>
      <div class="field">Name</div>
      <div class="field">Email Address</div>
      <div class="field">Phone Number</div>
      <div class="field query">Query<span class="go">GO</span></div>
    </section>
  </div>
</main>

<footer class="site-footer">
  <div class="wrap">
    <div class="foot-about">
      <h3>ABOUT US</h3>
      <div class="foot-cols">
        <ul><li>Home</li><li>About Us</li><li>Services</li><li>Human Resources</li></ul>
        <ul><li>Consultancy</li><li>Careers</li><li>Contact Us</li><li>Testimonials</li></ul>
        <ul><li>Privacy Policy</li><li>Disclaimer</li></ul>
      </div>
    </div>
    <div class="foot-touch">
      <h3>KEEP IN TOUCH</h3>
      <ul><li>MRHC, LLC.</li><li>P.O. Box 20415</li><li>Riverton, NM 87000</li><li>(505) 555-0148</li></ul>
    </div>
    <div class="foot-social">
      <h3>SOCIAL WITH US</h3>
      <div class="social-foot" aria-label="Social links"><span></span><span></span><span></span><span></span></div>
    </div>
  </div>
</footer>
<div class="copyright">Copyright © 2014 Mesa Ridge HR Consulting. All rights reserved</div>

</body>
</html>
```